Business Card Design Project

We need a Business Card for an Mechanical Engineering firm in Singapore. The design should be Modern & Technical looking, yet eye catching.

Our company deals in Cutting Tools & Machine Accessories for the Manufacturing Industries such as Oil & Gas, Aero Space, etc... For more information on our Company, you can either email me or view our website www.torvalen.com.sg.

We are trying to revamp our image to give our consumers a fresh new perspective to our company, so we welcome all ideas.

Industry/Entity Type

Business

Requirements
Must have
• Must incorporate New Company Logo into the card as shown in Uploaded file.

```html
<!DOCTYPE html>
<html lang="en">
<head>
<meta charset="utf-8">
<title>Torvalen Tools – Business Card</title>
<link rel="stylesheet" href="https://fonts.googleapis.com/css2?family=Mulish:wght@400;700&display=swap">
<style>
  :root {
    --backdrop: #0a090d;
    --card: #ffffff;
    --maroon-dark: #3d1018;
    --crimson: #9b1b35;
    --blush: #ebcdc8;
    --blush-soft: #f4e2df;
  }
  * { margin: 0; padding: 0; box-sizing: border-box; }
  html, body {
    width: 1200px;
    height: 1200px;
    overflow: hidden;
    background: var(--backdrop);
    font-family: "Mulish", sans-serif;
  }
  .stage { position: relative; width: 1200px; height: 1200px; }
  .card {
    position: absolute;
    top: 443px;
    width: 521px;
    height: 313px;
    background: var(--card);
    overflow: hidden;
  }
  .card--front { left: 54px; }
  .card--back { left: 624px; }

  /* Front */
  .brand {
    position: absolute;
    left: 0;
    right: 0;
    top: 178px;
    display: flex;
    justify-content: center;
    align-items: center;
    gap: 12px;
  }
  .brand__dot {
    width: 22px;
    height: 22px;
    border-radius: 50%;
    background: var(--crimson);
  }
  .brand__name {
    font-size: 32px;
    font-weight: 700;
    letter-spacing: 1px;
    color: var(--maroon-dark);
    line-height: 1;
  }
  .front__rule {
    position: absolute;
    left: 0;
    right: 0;
    top: 231px;
    height: 1px;
    background: var(--maroon-dark);
  }

  /* Back */
  .back__decor {
    position: absolute;
    right: 0;
    top: 0;
    width: 250px;
    height: 208px;
    background: linear-gradient(135deg, var(--blush-soft), var(--blush));
    border-bottom-left-radius: 120px;
  }
  .person { position: absolute; left: 39px; top: 38px; }
  .person__name {
    font-size: 26px;
    font-weight: 700;
    color: var(--maroon-dark);
    line-height: 1.1;
  }
  .person__role {
    font-size: 15px;
    color: var(--crimson);
    line-height: 1.3;
  }
  .contact {
    position: absolute;
    left: 39px;
    font-size: 14px;
    line-height: 16.5px;
    color: var(--crimson);
  }
  .contact--address { top: 156px; }
  .contact--lines { top: 208px; }
</style>
</head>
<body>
<main class="stage">
  <section class="card card--front" aria-label="Card front">
    <div class="brand">
      <span class="brand__dot"></span>
      <span class="brand__name">TORVALEN TOOLS</span>
    </div>
    <div class="front__rule"></div>
  </section>

  <section class="card card--back" aria-label="Card back">
    <div class="back__decor" role="img" aria-label="Large faint brand decoration in pale pink"></div>
    <div class="person">
      <p class="person__name">John DOE</p>
      <p class="person__role">Director</p>
    </div>
    <address class="contact contact--address" style="font-style:normal">
      dummy&nbsp; dummy<br>
      dummy dummy City dummy
    </address>
    <p class="contact contact--lines">
      (083) 123456<br>
      (083) 1234567<br>
      john@torvalentools.com<br>
      www.torvalentools.com
    </p>
  </section>
</main>
</body>
</html>
```